Animal Eye Clinic needs a Business card

We are a new veterinary ophthalmology practice (Ridgeline Pet Vision Care) and we need a business card designed. We only see animal eyes - we are not a regular veterinary clinic. We already have a logo. We are looking for a professional, good looking business card to hand out to our clients. We are looking for something simple but professional and contemporary. Our logo is likely the only picture/graphic that needs to be on the card.
Updates

Contact Information for Business Card

Delia Vossman, BSc, DVM, MSc, DipACVO
Veterinary Ophthalmologist

Phone: 250.418.3927
Email: ridgelinepetvisioncare@mailbox-example.net
Website: ridgelinepetvisioncare-example.net
Address: 1874 Thornbury Rd
Kelowna, BC, V1X 4M9

Colors

Designer to choose colors to be used in the design.

Requirements
Must have
• Our logo (attached)

```html
<!DOCTYPE html>
<html lang="en">
<head>
<meta charset="utf-8">
<title>Ridgeline Pet Vision Care – Business Card</title>
<link rel="stylesheet" href="https://fonts.googleapis.com/css2?family=Arimo:wght@400;700&display=swap">
<style>
  :root {
    --teal: #0e97a8;
    --grey: #7a7a7a;
    --ink: #5a5a5a;
    --rule: #9a9a9a;
    --paper: #ffffff;
    --backdrop: #2a2a2a;
  }
  * { box-sizing: border-box; margin: 0; padding: 0; }
  html, body { width: 1200px; height: 880px; overflow: hidden; }
  body {
    background: var(--backdrop);
    font-family: "Arimo", Arial, sans-serif;
    position: relative;
  }
  .card {
    position: absolute;
    width: 620px;
    height: 354px;
    background: var(--paper);
    border-radius: 18px;
    overflow: hidden;
    box-shadow: 0 10px 30px rgba(0,0,0,.45);
  }
  .card--front { left: 110px; top: 50px; }
  .card--back { left: 470px; top: 460px; }

  .brand { display: flex; align-items: center; gap: 14px; color: var(--teal); font-weight: 700; white-space: nowrap; }
  .brand__mark { border-radius: 50%; background: var(--teal); flex: none; }
  .card--front .brand { position: absolute; left: 0; right: 0; top: 150px; justify-content: center; font-size: 30px; }
  .card--front .brand__mark { width: 48px; height: 48px; }

  .back-art { position: absolute; inset: 0; }
  .social { position: absolute; right: 34px; top: 30px; display: flex; gap: 6px; }
  .social__item { width: 24px; height: 24px; background: var(--paper); border-radius: 3px; }

  .card--back .brand { position: absolute; left: 34px; top: 164px; font-size: 22px; gap: 10px; }
  .card--back .brand__mark { width: 36px; height: 36px; }

  .person { position: absolute; left: 34px; top: 218px; white-space: nowrap; }
  .person__name { color: var(--teal); font-size: 17px; line-height: 22px; }
  .person__name strong { font-weight: 700; }
  .person__role { color: var(--ink); font-size: 13px; line-height: 18px; margin-top: 2px; }

  .divider { position: absolute; left: 230px; right: 30px; top: 254px; height: 1px; background: var(--rule); }

  .address {
    position: absolute; right: 30px; top: 264px;
    text-align: right; color: var(--ink);
    font-size: 12.5px; line-height: 1.45; font-style: normal; white-space: nowrap;
  }

  .contacts { position: absolute; left: 34px; top: 270px; list-style: none; color: var(--ink); font-size: 12.5px; white-space: nowrap; }
  .contacts li { display: flex; align-items: center; gap: 8px; height: 20px; }
  .contacts svg { width: 13px; height: 13px; flex: none; }
</style>
</head>
<body>

<section class="card card--front" aria-label="Card front">
  <div class="brand"><span class="brand__mark"></span><span class="brand__name">Ridgeline Pet Vision Care</span></div>
</section>

<section class="card card--back" aria-label="Card back">
  <svg class="back-art" viewBox="0 0 620 354" preserveAspectRatio="none" aria-hidden="true">
    <path d="M0 0 H620 V150 Q420 60 0 135 Z" fill="var(--teal)"/>
    <path d="M620 150 Q420 60 0 135 L0 142 Q420 72 620 168 Z" fill="var(--grey)"/>
  </svg>

  <div class="social">
    <span class="social__item"></span><span class="social__item"></span><span class="social__item"></span>
  </div>

  <div class="brand"><span class="brand__mark"></span><span class="brand__name">Ridgeline Pet Vision Care</span></div>

  <div class="person">
    <p class="person__name"><strong>Delia Vossman</strong>, BSc, DVM, MSc, DipACVO</p>
    <p class="person__role">Veterinary Ophthalmologist</p>
  </div>

  <div class="divider"></div>

  <address class="address">1874 Thornbury Rd<br>Kelowna, BC, V1X 4M9</address>

  <ul class="contacts">
    <li>
      <svg viewBox="0 0 14 14"><rect x="3" y="1" width="8" height="12" rx="1.5" fill="none" stroke="var(--teal)" stroke-width="1.5"/></svg>
      250.418.3927
    </li>
    <li>
      <svg viewBox="0 0 14 14"><rect x="1" y="3" width="12" height="8" fill="var(--teal)"/><path d="M1 3 L7 8 L13 3" fill="none" stroke="#fff" stroke-width="1"/></svg>
      ridgelinepetvisioncare@mailbox-example.net
    </li>
    <li>
      <svg viewBox="0 0 14 14"><circle cx="7" cy="7" r="6" fill="var(--teal)"/><path d="M1 7 H13 M7 1 V13 M3 3.5 Q7 6 11 3.5 M3 10.5 Q7 8 11 10.5" fill="none" stroke="#fff" stroke-width=".8"/></svg>
      ridgelinepetvisioncare-example.net
    </li>
  </ul>
</section>

</body>
</html>
```